Upscale business cards needed for Board of Directors

We need professional business cards created for members of our family business Board of Directors. We would like these relatively simple and straightforward, but also with a unique element to set them apart. Probably stick with neutral and simple colors - white, grey etc. We need space for the traditional elements, including name, title, address, email/phone number. And we will be creating several from this template so it needs to be template that is easy to switch information in and out of.
Business
See description

```html
<!DOCTYPE html>
<html lang="en">
<head>
<meta charset="utf-8">
<title>Harborline Holdings – Business Card</title>
<link rel="stylesheet" href="https://fonts.googleapis.com/css2?family=Open+Sans:wght@400;600;700&display=swap">
<style>
  :root {
    --backdrop: #3b3531;
    --card: #0d0d0d;
    --card-edge: #1a1a1a;
    --white: #f2f2f2;
    --gold: #c7a86d;
  }
  * { box-sizing: border-box; margin: 0; padding: 0; }
  html, body {
    width: 1200px; height: 844px; overflow: hidden;
    background: var(--backdrop);
    font-family: "Open Sans", Arial, sans-serif;
  }
  .stage { position: relative; width: 1200px; height: 844px; }
  .card {
    position: absolute; top: 273px;
    width: 525px; height: 300px;
    background: var(--card);
    border: 1px solid var(--card-edge);
    box-shadow: 0 10px 30px rgba(0,0,0,.45);
  }
  .card--front { left: 45px; }
  .card--back  { left: 630px; }

  .brand {
    position: absolute; left: 0; right: 0;
    display: flex; flex-direction: column; align-items: center;
  }
  .brand__rule {
    width: 340px; height: 4px; background: var(--gold);
    margin-bottom: 10px;
  }
  .brand__name {
    color: var(--white); font-size: 26px; font-weight: 700;
    letter-spacing: 2px; text-transform: uppercase; line-height: 1;
    white-space: nowrap;
  }
  .card--front .brand { top: 70px; }
  .card--back .brand  { top: 128px; }

  .contact-list {
    position: absolute; right: 26px; top: 150px;
    list-style: none; text-align: right;
    font-size: 12.5px; color: var(--white); line-height: 23px;
  }
  .contact-list li { display: flex; justify-content: flex-end; align-items: center; gap: 8px; }
  .contact-list svg { width: 11px; height: 11px; fill: var(--gold); flex: none; }

  .person {
    position: absolute; left: 30px; bottom: 34px;
    color: var(--white); font-size: 13.5px; line-height: 17px;
  }
  .person__name { color: var(--gold); font-size: 17px; font-weight: 600; line-height: 21px; }
  .person__address { margin-top: 18px; }
</style>
</head>
<body>
<main class="stage">

  <section class="card card--front" aria-label="Business card front">
    <div class="brand">
      <span class="brand__rule"></span>
      <span class="brand__name">Harborline Holdings</span>
    </div>

    <ul class="contact-list">
      <li>(044)-555-0182
        <svg viewBox="0 0 24 24" aria-hidden="true"><path d="M6.6 10.8a15.1 15.1 0 0 0 6.6 6.6l2.2-2.2a1 1 0 0 1 1-.25 11.4 11.4 0 0 0 3.6.57 1 1 0 0 1 1 1V20a1 1 0 0 1-1 1A17 17 0 0 1 3 4a1 1 0 0 1 1-1h3.5a1 1 0 0 1 1 1c0 1.25.2 2.45.57 3.6a1 1 0 0 1-.25 1z"/></svg>
      </li>
      <li>info@harborline.com
        <svg viewBox="0 0 24 24" aria-hidden="true"><rect x="2" y="5" width="20" height="14"/><path d="M2 5l10 8 10-8" fill="none" stroke="#0d0d0d" stroke-width="2"/></svg>
      </li>
      <li>www.harborline.com
        <svg viewBox="0 0 24 24" aria-hidden="true"><circle cx="12" cy="12" r="11"/><path d="M1 12h22M12 1c4 4 4 18 0 22M12 1c-4 4-4 18 0 22" fill="none" stroke="#0d0d0d" stroke-width="1.6"/></svg>
      </li>
    </ul>

    <div class="person">
      <p class="person__name">Daniel Whitford</p>
      <p class="person__title">Managing Director</p>
      <p class="person__address">12345, Address Goes Here<br>Country Name, 123456</p>
    </div>
  </section>

  <section class="card card--back" aria-label="Business card back">
    <div class="brand">
      <span class="brand__rule"></span>
      <span class="brand__name">Harborline Holdings</span>
    </div>
  </section>

</main>
</body>
</html>
```